Progressive European Honey Business needs minimalistic packaging design

Hello - thank you for your interest in our brief. We are Honey Plinks, a London based Honey business, importing only the best honey Europe has to offer. Our values are deeply rooted with in progressive liberal values and we are looking for minimalist packaging, which reflects that.

We are looking for a design, which dimensions fit with our packaging option (Vessio Glass Jar | HEIGHT 90mm | DIAMETER 63mm). We will require a various output files (High Resolution JPEG (CMYK Colors 300 dpi) Source File Ai, PSD, PDF, Printing files (die cut, die folding) and a 3D Mockup of the packaging for use within digital commerce platforms.

We must be able to adjust the free text on the label front and it should include the following:
Brand Name
Honey type
Limited edition No. X / 100 ( X being the number of purchase i.e. 25 / 100)
EU Honey, Single Orgin (Germany)
(c) The net weight (250g)

The back must include room for additional information (again adjustable by us) and the following:
“Unsuitable for children under 12 months”
(b) The appropriate durability declaration

In total, we are looking for
a) A front label
b) A back label
c) A seal (round) including the attached bee and logo included in the Zip file.
Do note that a) & b) can also be combined into one design as long as the symmetry on the jar stays intact.

The final design should communicate modern aesthetics, high quality, that are slightly provocative and pop off the shelves.

Hi folks, sorry for the delay in completing this project, but my business partner had a leak in his house. We planned to finalise our review today, but this will have to wait until it's no longer raining in his livingroom. Our sincere apologies!

• See branding guidelines

• Must follow the branding guideline and fonts provided as attachment

```html
<!DOCTYPE html>
<html lang="en">
<head>
<meta charset="utf-8">
<title>Honey Plinks – Lavender Honey Front Label</title>
<link rel="stylesheet" href="https://fonts.googleapis.com/css2?family=Josefin+Sans:wght@700&family=Jost:wght@400;600&display=swap">
<style>
  :root {
    --backdrop: #e9e9ea;
    --plum-deep: #1f1420;
    --plum-mid: #2e1f30;
    --plum-soft: #4c3a52;
    --lavender: #8e5fa8;
    --lavender-light: #b58ccc;
    --sky: #dfe3e6;
    --ink-light: #ececee;
    --ink-muted: #d9d6dc;
    --badge-yellow: #f2e03a;
    --badge-ink: #3a2e14;
    --rule-yellow: #cfc23a;
  }
  * { margin: 0; padding: 0; box-sizing: border-box; }
  html, body {
    width: 1200px;
    height: 960px;
    overflow: hidden;
    background: var(--backdrop);
  }
  .label {
    position: absolute;
    left: 228px;
    top: 30px;
    width: 744px;
    height: 900px;
    overflow: hidden;
    background: var(--plum-mid);
  }
  .label-scenery {
    position: absolute;
    left: 0; top: 0;
    width: 744px;
    height: 320px;
    background: linear-gradient(180deg,
      var(--sky) 0%, #c9ced4 30%, #8c8aa0 36%,
      var(--lavender-light) 44%, var(--lavender) 100%);
  }
  .label-panel {
    position: absolute;
    left: 0; top: 0;
    width: 744px;
    height: 900px;
  }
  .edition-badge {
    position: absolute;
    left: 34px;
    top: 300px;
    width: 120px;
    height: 120px;
    border-radius: 50%;
    background: var(--badge-yellow);
    display: flex;
    flex-direction: column;
    align-items: center;
    justify-content: center;
    font-family: "Jost", sans-serif;
    font-weight: 600;
    color: var(--badge-ink);
    line-height: 1.1;
    text-align: center;
    transform: rotate(-14deg);
  }
  .edition-badge .edition-word { font-size: 19px; letter-spacing: 0.5px; }
  .edition-badge .edition-number { font-size: 14px; margin-top: 4px; }
  .brand-name {
    position: absolute;
    left: 12px;
    top: 530px;
    font-family: "Jost", sans-serif;
    font-weight: 600;
    font-size: 86px;
    line-height: 1;
    color: var(--ink-light);
    white-space: nowrap;
    letter-spacing: 1px;
  }
  .honey-type {
    position: absolute;
    left: 12px;
    top: 770px;
    font-family: "Josefin Sans", sans-serif;
    font-weight: 700;
    font-size: 36px;
    letter-spacing: 9px;
    color: var(--ink-light);
  }
  .origin-line {
    position: absolute;
    left: 12px;
    top: 826px;
    font-family: "Jost", sans-serif;
    font-weight: 400;
    font-size: 26px;
    color: var(--ink-muted);
    display: flex;
    align-items: center;
    gap: 8px;
  }
  .origin-dot {
    width: 14px; height: 14px;
    border-radius: 50%;
    background: var(--ink-muted);
  }
  .net-weight {
    position: absolute;
    right: 46px;
    top: 826px;
    font-family: "Jost", sans-serif;
    font-weight: 600;
    font-size: 27px;
    color: var(--ink-light);
  }
  .label-rule {
    position: absolute;
    left: 0; right: 0;
    top: 880px;
    height: 2px;
    background: var(--rule-yellow);
  }
</style>
</head>
<body>
  <main class="label">
    <div class="label-scenery" role="img" aria-label="Photograph of a lavender field in rows under a pale sky with distant hills"></div>

    <svg class="label-panel" viewBox="0 0 744 900" aria-hidden="true">
      <defs>
        <linearGradient id="panelShade" x1="0" y1="0" x2="1" y2="0">
          <stop offset="0" stop-color="#4c3a52"/>
          <stop offset="0.45" stop-color="#1f1420"/>
          <stop offset="1" stop-color="#3a2b3e"/>
        </linearGradient>
      </defs>
      <path fill="url(#panelShade)" d="M0,250 Q372,190 744,250 L744,900 L0,900 Z"/>
    </svg>

    <div class="edition-badge">
      <span class="edition-word">LIMITED</span>
      <span class="edition-word">EDITION</span>
      <span class="edition-number">No. X / 100</span>
    </div>

    <h1 class="brand-name">HONEY PLINKS</h1>
    <p class="honey-type">LAVENDER HONEY</p>
    <p class="origin-line">EU Honey <span class="origin-dot"></span> Single Orgin (Germany)</p>
    <p class="net-weight">250g</p>
    <div class="label-rule"></div>
  </main>
</body>
</html>
```